Park furniture company needs a new product flyer

We're a street and park furniture supply company and we have a new range of furniture that we would like to showcase to prospective customers.
Pictures, logo and copy attached.
Furniture pictures are also available with a black background.
Warranty information needs to feature on the flyer.
Recycled content information needs to feature on the flyer.

Target Market(s)

Landscape Architects

Font styles to use
Serif

Requirements
Must have
• Professional fonts and graphics.
Should not have
• comic sans or similar fonts - cheap graphics

```html
<!DOCTYPE html>
<html lang="en">
<head>
<meta charset="utf-8">
<title>Kerbline Commons – Product Flyer</title>
<link rel="stylesheet" href="https://fonts.googleapis.com/css2?family=Montserrat:wght@300;400;700&family=Oswald:wght@400;600;700&display=swap">
<style>
:root{
  --blue:#2f7bc4;
  --red:#c90a0e;
  --red-dark:#a3242a;
  --slate:#58585a;
  --logo-grey:#545456;
  --paper:#ffffff;
  --mist:#ececec;
  --frame:#b3b3b3;
  --wood:#a8521c;
  --wood-light:#cf7a3a;
  --steel:#b9ad98;
}
*{margin:0;padding:0;box-sizing:border-box}
html,body{width:960px;height:1200px;overflow:hidden;background:var(--paper)}
.flyer{position:relative;width:960px;height:1200px;overflow:hidden;font-family:"Montserrat",sans-serif;
  background:linear-gradient(135deg,#f4f4f4 0%,#ffffff 45%,#f1f1f1 100%)}

.brand{position:absolute;left:85px;top:88px;display:flex;align-items:center;gap:14px}
.brand-mark{width:34px;height:34px;background:var(--blue)}
.brand-name{font-weight:700;font-size:40px;letter-spacing:1px;color:var(--logo-grey);line-height:1}

.hero-band{position:absolute;left:0;top:198px;width:680px;height:301px;background:var(--blue)}
.hero-copy{position:absolute;left:70px;top:228px;color:#fff;font-weight:300;font-size:35px;line-height:45px}
.hero-copy strong{font-weight:700}
.hero-copy .closing{font-weight:700;font-size:43px;line-height:52px;display:block}

.warranty-band{position:absolute;left:0;top:499px;width:680px;height:86px;
  background:linear-gradient(90deg,var(--red) 0%,#dc1116 55%,var(--red-dark) 100%)}
.warranty{position:absolute;left:71px;top:484px;width:533px;height:89px;border:2px solid #fff;
  display:flex;align-items:center;justify-content:center;
  font-family:"Oswald",sans-serif;font-weight:700;font-size:62px;color:#fff;letter-spacing:0.5px}

.hero-photo{position:absolute;left:499px;top:74px;width:414px;height:515px;
  background:linear-gradient(160deg,var(--wood-light) 0%,var(--wood) 55%,var(--steel) 100%);
  clip-path:polygon(40% 0,100% 28%,94% 100%,80% 100%,40% 70%,0 25%)}

.spec-panel{position:absolute;left:377px;top:585px;width:583px;height:549px;background:var(--slate)}
.spec-wedge{position:absolute;left:0;top:0;width:960px;height:1200px;pointer-events:none}

.gallery{position:absolute;left:0;top:585px;width:377px;height:549px;
  background:linear-gradient(135deg,#f3f3f3,#e6e6e6 50%,#f6f6f6)}
.thumb{position:absolute;left:71px;width:259px;height:154px;border:9px solid var(--frame);background:#fff;
  box-shadow:0 6px 8px rgba(0,0,0,.12)}
.thumb span{display:block;width:100%;height:100%}
.thumb-1{top:611px}.thumb-2{top:787px}.thumb-3{top:963px}
.thumb-1 span{background:linear-gradient(180deg,#fff 10%,#6e5e50 30%,#cfc6b7 70%,#fff 95%)}
.thumb-2 span{background:linear-gradient(180deg,#fff 8%,#b4581f 25%,#c46a2b 60%,#d7cdbd 80%,#fff 95%)}
.thumb-3 span{background:linear-gradient(160deg,#fff 10%,#7a6b5c 40%,#cfc6b7 75%,#fff 95%)}

.features{position:absolute;left:0;top:0;list-style:none;color:#fff;font-size:14.6px;line-height:21.5px}
.features::before{content:"";position:absolute;left:444px;top:630px;width:1px;height:380px;background:#cfcfcf}
.feature{position:absolute;left:434px;width:470px;padding-left:27px}
.feature svg{position:absolute;left:0;top:0;width:21px;height:21px;background:var(--slate)}
.feature p{font-size:14.6px}
.feature.compact p{font-size:13.4px;line-height:19px}

.call-bar{position:absolute;left:377px;top:1051px;width:583px;height:61px;background:#fff;
  display:flex;align-items:center;justify-content:center;gap:14px;
  font-family:"Oswald",sans-serif;font-weight:600;font-size:44px;color:var(--blue)}
.call-bar svg{width:52px;height:52px}

.web-bar{position:absolute;left:0;top:1134px;width:960px;height:66px;background:var(--blue);
  display:flex;align-items:center;justify-content:center;gap:14px;
  font-family:"Oswald",sans-serif;font-weight:400;font-size:36px;color:#fff;letter-spacing:0.3px}
.web-bar svg{width:36px;height:36px}
</style>
</head>
<body>
<main class="flyer">

  <div class="brand">
    <span class="brand-mark"></span>
    <span class="brand-name">KERBLINE COMMONS</span>
  </div>

  <div class="hero-band"></div>
  <p class="hero-copy">
    European <strong>inspired</strong><br>
    with a <strong>unique</strong> and<br>
    <strong>original design</strong>, that is<br>
    functional all while respecting<br>
    <span class="closing">the Environment.</span>
  </p>

  <div class="warranty-band"></div>
  <div class="warranty">10-YEAR WARRANTY</div>

  <div class="spec-panel"></div>
  <svg class="spec-wedge" viewBox="0 0 960 1200" aria-hidden="true">
    <polygon points="680,585 960,514 960,585" fill="#58585a"/>
  </svg>

  <div class="hero-photo" role="img" aria-label="Photo of a park bench with timber-look composite seat and backrest, armrests and a champagne aluminium frame"></div>

  <div class="gallery"></div>
  <div class="thumb thumb-1"><span role="img" aria-label="Photo of a picnic table with matching bench seat in dark composite battens"></span></div>
  <div class="thumb thumb-2"><span role="img" aria-label="Photo of a front view of the bench seat with backrest and armrests"></span></div>
  <div class="thumb thumb-3"><span role="img" aria-label="Photo of a table set with two separate benches shown from above"></span></div>

  <ul class="features">
    <li class="feature" style="top:619px"><svg viewBox="0 0 22 22"><circle cx="11" cy="11" r="9.5" fill="none" stroke="#fff" stroke-width="1.6"/><path d="M6.5 11.2l3 3 6-6" fill="none" stroke="#fff" stroke-width="1.8"/></svg>
      <p>Our range is designed to make life easier for people; created using extremely durable, ultra low maintenance materials.</p></li>
    <li class="feature" style="top:693px"><svg viewBox="0 0 22 22"><circle cx="11" cy="11" r="9.5" fill="none" stroke="#fff" stroke-width="1.6"/><path d="M6.5 11.2l3 3 6-6" fill="none" stroke="#fff" stroke-width="1.8"/></svg>
      <p>Featuring 98% recycled composite battens in a range of stain and fade-resistant colour options and a unique aluminium frame design.</p></li>
    <li class="feature" style="top:770px"><svg viewBox="0 0 22 22"><circle cx="11" cy="11" r="9.5" fill="none" stroke="#fff" stroke-width="1.6"/><path d="M6.5 11.2l3 3 6-6" fill="none" stroke="#fff" stroke-width="1.8"/></svg>
      <p>The capped composite battens come with a 10-year commercial warranty covering staining, fading and structural performance.</p></li>
    <li class="feature" style="top:846px"><svg viewBox="0 0 22 22"><circle cx="11" cy="11" r="9.5" fill="none" stroke="#fff" stroke-width="1.6"/><path d="M6.5 11.2l3 3 6-6" fill="none" stroke="#fff" stroke-width="1.8"/></svg>
      <p>Site-specific for healthcare applications offering wheelchair accessibility options</p></li>
    <li class="feature compact" style="top:903px"><svg viewBox="0 0 22 22"><circle cx="11" cy="11" r="9.5" fill="none" stroke="#fff" stroke-width="1.6"/><path d="M6.5 11.2l3 3 6-6" fill="none" stroke="#fff" stroke-width="1.8"/></svg>
      <p>The Kerbline Commons range comprises of a seat with optional armrests, bench seat and table, available in both standard or DDA designs.</p></li>
    <li class="feature compact" style="top:973px"><svg viewBox="0 0 22 22"><circle cx="11" cy="11" r="9.5" fill="none" stroke="#fff" stroke-width="1.6"/><path d="M6.5 11.2l3 3 6-6" fill="none" stroke="#fff" stroke-width="1.8"/></svg>
      <p>Uniform length of 1800mm with tailored options available.</p></li>
    <li class="feature compact" style="top:1007px"><svg viewBox="0 0 22 22"><circle cx="11" cy="11" r="9.5" fill="none" stroke="#fff" stroke-width="1.6"/><path d="M6.5 11.2l3 3 6-6" fill="none" stroke="#fff" stroke-width="1.8"/></svg>
      <p>Bolt down or freestanding options.</p></li>
  </ul>

  <div class="call-bar">
    <span>CALL US</span>
    <svg viewBox="0 0 52 52" aria-hidden="true"><circle cx="26" cy="26" r="23.5" fill="none" stroke="#2f7bc4" stroke-width="4"/><path d="M19 14c2-1 3 0 4 2l2 4c.5 1.5-.5 2.5-1.5 3.2 1 3 3 5.5 6 7 .8-1 2-2 3.4-1.4l4 2c2 1 2.4 2.2 1.4 4-1.5 2.5-4 3.4-7 2.4-7-2.5-12-8-14-15-.8-3 .2-6.5 1.7-8.2z" fill="none" stroke="#2f7bc4" stroke-width="3"/></svg>
    <span>0400 555 218</span>
  </div>

  <div class="web-bar">
    <span>FOR MORE INFORMATION VISIT</span>
    <svg viewBox="0 0 36 36" aria-hidden="true" fill="none" stroke="#fff" stroke-width="2"><circle cx="18" cy="18" r="15"/><ellipse cx="18" cy="18" rx="7" ry="15"/><line x1="3" y1="18" x2="33" y2="18"/><path d="M6 10h24M6 26h24"/></svg>
    <span>WWW.KERBLINECOMMONS.COM.AU</span>
  </div>

</main>
</body>
</html>
```